Tech business card design

We need an amazing business card design for our new business 'Pexla' a marketing tech startup based in Sydney, Australia. We provide an online marketplace for businesses to search and buy advertising media, connect with service providers and learn more about marketing. We wish to communicate 'cool tech', reliability and professionalism and design based around our logo.

Target Market(s)

Business Owners

Contact Information for Business Card

Name
Position
Email Address
Website
Phone Number

Font styles to use
Other font styles liked:
• Avenir & Avenir Next

Colors

Designer to choose colors to be used in the design.

```html
<!DOCTYPE html>
<html lang="en">
<head>
<meta charset="UTF-8">
<title>Pexla Business Card</title>
<link rel="stylesheet" href="https://fonts.googleapis.com/css2?family=Nunito+Sans:wght@400;800&display=swap">
<style>
  :root {
    --navy: #0a0838;
    --paper: #f6f6f6;
    --ink-light: #ffffff;
    --ghost: rgba(255, 255, 255, 0.14);
    --backdrop: #e8e6e2;
    --shadow: rgba(20, 16, 40, 0.22);
  }
  * { margin: 0; padding: 0; box-sizing: border-box; }
  html, body {
    width: 1200px;
    height: 900px;
    overflow: hidden;
    background: var(--backdrop);
    font-family: "Nunito Sans", sans-serif;
  }
  .sheet {
    width: 1200px;
    height: 900px;
    display: flex;
    flex-direction: column;
    align-items: center;
    justify-content: center;
    gap: 44px;
  }
  .card {
    position: relative;
    width: 640px;
    height: 390px;
    overflow: hidden;
    box-shadow: 0 10px 28px var(--shadow);
  }
  /* Back of card */
  .card-back {
    background: var(--navy);
    display: flex;
    flex-direction: column;
    align-items: center;
    justify-content: center;
    gap: 10px;
  }
  .card-back .brand-name {
    font-weight: 800;
    font-size: 84px;
    line-height: 1;
    color: var(--ink-light);
    letter-spacing: -1px;
  }
  .card-back .web {
    font-weight: 800;
    font-size: 24px;
    color: var(--ink-light);
    letter-spacing: 0.5px;
  }
  /* Front of card */
  .card-front {
    display: flex;
    background: var(--navy);
  }
  .brand-panel {
    width: 40%;
    height: 100%;
    background: var(--paper);
    display: flex;
    align-items: center;
    justify-content: center;
  }
  .brand-panel .brand-name {
    font-weight: 800;
    font-size: 70px;
    line-height: 1;
    color: var(--navy);
    letter-spacing: -1px;
  }
  .details {
    position: relative;
    flex: 1;
    color: var(--ink-light);
    padding: 30px 30px 28px 0;
    display: flex;
    flex-direction: column;
    justify-content: space-between;
    align-items: flex-end;
    text-align: right;
  }
  .ghost-name {
    position: absolute;
    left: -20px;
    top: 120px;
    font-weight: 800;
    font-size: 150px;
    line-height: 1;
    color: var(--ghost);
    letter-spacing: -2px;
    white-space: nowrap;
    pointer-events: none;
  }
  .person { position: relative; }
  .person .name {
    font-size: 30px;
    font-weight: 400;
    letter-spacing: 0.5px;
    line-height: 1.15;
  }
  .person .role {
    font-size: 20px;
    font-weight: 400;
    letter-spacing: 0.5px;
  }
  .contact {
    position: relative;
    list-style: none;
    font-size: 20px;
    line-height: 1.4;
    letter-spacing: 0.3px;
  }
</style>
</head>
<body>
<main class="sheet">
  <section class="card card-back" aria-label="Card back">
    <div class="brand-name">Pexla</div>
    <div class="web">www.pexlamedia.com.au</div>
  </section>

  <section class="card card-front" aria-label="Card front">
    <div class="brand-panel">
      <div class="brand-name">Pexla</div>
    </div>
    <div class="details">
      <div class="ghost-name" aria-hidden="true">Pexla</div>
      <div class="person">
        <div class="name">Daniel Marsh</div>
        <div class="role">Founder, Director</div>
      </div>
      <ul class="contact">
        <li>+61 (0)412 555 208</li>
        <li>daniel@pexlamedia.com.au</li>
        <li>www.pexlamedia.com.au</li>
      </ul>
    </div>
  </section>
</main>
</body>
</html>
```